Packaging for educational products for special needs kids - Drawer (pull-out) box

1. Modern, minimalist but attractive packaging for educational products for kids.
2. Approx size 24 x 15.5 x 2 cm.
3. Please refer to the sample packaging image for the kind of information that will be placed on the box. But the new designed box will be white.
4. The background on the sample images of a boy and a girl is used on all the cards so you can refer to this colour to be used in your designs.

Font styles to use
Sans Serif

Colors
87cfc6
cfeae6
f04a50
faa54b
fbee3d
abd036
00a990

```html
<!DOCTYPE html>
<html lang="en">
<head>
<meta charset="utf-8">
<title>Visual Schedules – Drawer Box Lids</title>
<link href="https://fonts.googleapis.com/css2?family=Cabin+Sketch:wght@700&family=Roboto+Condensed:wght@700&display=swap" rel="stylesheet">
<style>
  :root {
    --stage: #949494;
    --lid: #f7f7f7;
    --lid-edge: #e6e6e6;
    --slate: #4a6478;
    --slate-soft: #8fa3b3;
    --coral: #e0505c;
    --coral-soft: #f09aa0;
    --orange: #f5a33f;
    --mint: #87cfc6;
    --mint-pale: #cfeae6;
    --white: #ffffff;
  }
  * { margin: 0; padding: 0; box-sizing: border-box; }
  html, body { width: 1200px; height: 1047px; overflow: hidden; }
  body { background: var(--stage); position: relative; }

  .lid {
    position: absolute;
    width: 448px;
    height: 680px;
    background: var(--lid);
    box-shadow: inset 0 0 0 1px var(--lid-edge);
  }
  .lid--boys  { left: 90px;  top: 182px; --accent: var(--slate); --accent-soft: var(--slate-soft); --art: linear-gradient(160deg, var(--mint-pale), var(--mint) 55%, var(--slate-soft)); }
  .lid--girls { left: 658px; top: 90px;  --accent: var(--coral); --accent-soft: var(--coral-soft); --art: linear-gradient(160deg, #fde2e4, var(--coral-soft) 55%, var(--coral)); }

  .lid__art {
    position: absolute;
    left: 126px; top: 126px;
    width: 192px; height: 182px;
    border-radius: 18px;
    background: var(--art);
  }
  .lid__rule {
    position: absolute;
    left: 136px; width: 176px;
    border-top: 2px dotted var(--accent);
  }
  .lid__rule--top { top: 326px; }
  .lid__rule--bottom { top: 408px; }

  .lid__title {
    position: absolute;
    left: 0; width: 100%;
    text-align: center;
    font-family: "Cabin Sketch", sans-serif;
    font-weight: 700;
    color: var(--accent);
    line-height: 1;
  }
  .lid__title--main { top: 330px; font-size: 46px; letter-spacing: 1px; }
  .lid__title--sub  { top: 376px; font-size: 28px; letter-spacing: 0.5px; }
  .lid__by {
    position: absolute; top: 414px; left: 0; width: 100%;
    text-align: center;
    font-family: "Cabin Sketch", sans-serif; font-weight: 700;
    font-size: 22px; color: var(--orange);
  }
  .lid__brand {
    position: absolute; top: 444px; left: 0; width: 100%;
    text-align: center;
    font-family: "Cabin Sketch", sans-serif; font-weight: 700;
    font-size: 26px; color: var(--accent);
  }

  .lid__badge {
    position: absolute; top: 594px; left: 50%;
    transform: translateX(-50%);
    display: flex;
    border: 1.5px solid var(--accent);
    font-family: "Roboto Condensed", sans-serif; font-weight: 700;
    font-size: 11px; line-height: 16px;
  }
  .lid__badge-label { padding: 1px 5px; color: var(--accent); background: var(--white); }
  .lid__badge-value { padding: 1px 6px; color: var(--white); background: var(--accent); }

  .lid__care {
    position: absolute; top: 624px; left: 50%;
    transform: translateX(-50%);
    display: flex; gap: 5px;
  }
  .care-icon { width: 17px; height: 17px; }
  .care-icon circle { fill: none; stroke: var(--accent); stroke-width: 1.3; }
  .care-icon .glyph { fill: var(--accent); stroke: none; }
  .care-icon .glyph-line { fill: none; stroke: var(--accent); stroke-width: 1.3; }

  .lid__tab {
    position: absolute; bottom: -34px; left: 50%;
    transform: translateX(-50%);
    width: 14px; height: 34px;
    background: #dcdcdc;
  }
</style>
</head>
<body>

  <section class="lid lid--boys">
    <div class="lid__art" role="img" aria-label="Illustration of a cheerful boy stretching behind a calendar with the product name, a pillow and an alarm clock"></div>
    <div class="lid__rule lid__rule--top"></div>
    <h1 class="lid__title lid__title--main">VISUAL</h1>
    <h2 class="lid__title lid__title--sub">SCHEDULES</h2>
    <div class="lid__rule lid__rule--bottom"></div>
    <p class="lid__by">BY</p>
    <p class="lid__brand">Tiny Champs</p>
    <div class="lid__badge"><span class="lid__badge-label">Package For</span><span class="lid__badge-value">BOYS</span></div>
    <div class="lid__care">
      <svg class="care-icon" viewBox="0 0 18 18"><circle cx="9" cy="9" r="8"/><path class="glyph" d="M9 4 C11 7 12 9 12 10.5 A3 3 0 0 1 6 10.5 C6 9 7 7 9 4Z"/></svg>
      <svg class="care-icon" viewBox="0 0 18 18"><circle cx="9" cy="9" r="8"/><path class="glyph" d="M4.5 9 A4.5 4 0 0 1 13.5 9Z"/><path class="glyph-line" d="M9 9 V13 A1 1 0 0 1 7 13"/></svg>
      <svg class="care-icon" viewBox="0 0 18 18"><circle cx="9" cy="9" r="8"/><path class="glyph-line" d="M6 7 L9 4.5 L12 7 M12.5 9.5 L11 13 H7 L5.5 9.5"/></svg>
      <svg class="care-icon" viewBox="0 0 18 18"><circle cx="9" cy="9" r="8"/><path class="glyph" d="M5 13 C5 7 9 5 13 5 C13 10 10 13 5 13Z"/></svg>
      <svg class="care-icon" viewBox="0 0 18 18"><circle cx="9" cy="9" r="8"/><path class="glyph-line" d="M6.5 13 V5 M4.8 6.8 L6.5 5 L8.2 6.8 M11.5 13 V5 M9.8 6.8 L11.5 5 L13.2 6.8"/></svg>
    </div>
    <div class="lid__tab"></div>
  </section>

  <section class="lid lid--girls">
    <div class="lid__art" role="img" aria-label="Illustration of a cheerful girl stretching behind a calendar with the product name, a pillow and an alarm clock"></div>
    <div class="lid__rule lid__rule--top"></div>
    <h1 class="lid__title lid__title--main">VISUAL</h1>
    <h2 class="lid__title lid__title--sub">SCHEDULES</h2>
    <div class="lid__rule lid__rule--bottom"></div>
    <p class="lid__by">BY</p>
    <p class="lid__brand">Tiny Champs</p>
    <div class="lid__badge"><span class="lid__badge-label">Package For</span><span class="lid__badge-value">GIRLS</span></div>
    <div class="lid__care">
      <svg class="care-icon" viewBox="0 0 18 18"><circle cx="9" cy="9" r="8"/><path class="glyph" d="M9 4 C11 7 12 9 12 10.5 A3 3 0 0 1 6 10.5 C6 9 7 7 9 4Z"/></svg>
      <svg class="care-icon" viewBox="0 0 18 18"><circle cx="9" cy="9" r="8"/><path class="glyph" d="M4.5 9 A4.5 4 0 0 1 13.5 9Z"/><path class="glyph-line" d="M9 9 V13 A1 1 0 0 1 7 13"/></svg>
      <svg class="care-icon" viewBox="0 0 18 18"><circle cx="9" cy="9" r="8"/><path class="glyph-line" d="M6 7 L9 4.5 L12 7 M12.5 9.5 L11 13 H7 L5.5 9.5"/></svg>
      <svg class="care-icon" viewBox="0 0 18 18"><circle cx="9" cy="9" r="8"/><path class="glyph" d="M5 13 C5 7 9 5 13 5 C13 10 10 13 5 13Z"/></svg>
      <svg class="care-icon" viewBox="0 0 18 18"><circle cx="9" cy="9" r="8"/><path class="glyph-line" d="M6.5 13 V5 M4.8 6.8 L6.5 5 L8.2 6.8 M11.5 13 V5 M9.8 6.8 L11.5 5 L13.2 6.8"/></svg>
    </div>
    <div class="lid__tab"></div>
  </section>

</body>
</html>
```